Recruiting Firm Need Professional, Modern Tri-Fold Brochure for their United States Based Business

-We need a professional, modern TRI-FOLD brochure design that can help generate business for our recruiting firm. We need an impressive brochure.
- Please use the about us website content and attached website content. Website: www.morvellstaffingpartners.example
- Please use logo files attached.
- Please note: This brochure will be the starting point for an upgraded website design so we are NOT looking for a brochure to look like our current website.
- We want potential clients to want to do business with us just based on the brochure look and feel alone.

Target Market(s)

small, medium, and large companies who need administrative, human resources, and accounting talent

Industry/Entity Type

Professional Service

Font styles to use
Serif

Requirements
Must have
• - Professional, Modern TRI-FOLD Brochure Design for United States Based Company
• - Please show diverse group of professionals pictures similar to the ones on our website. One pic must include an African American female and one pic must include an African male. Or both an African American female and male can be include in the group of other races. But All the group photos must be diverse in race and include both male and female.
• - Please show pics of one business professional too
• a diverse group photo would be nice on the front cover...so we can show diversity and inclusion from the start
Should not have
• - Please DO NOT use the same pictures on our website.

```html
<!DOCTYPE html>
<html lang="en">
<head>
<meta charset="utf-8">
<title>Morvell Staffing Partners – Tri-Fold Brochure</title>
<link href="https://fonts.googleapis.com/css2?family=Open+Sans:wght@300;400;600;700&display=swap" rel="stylesheet">
<style>
  :root {
    --red: #c0141c;
    --red-deep: #8e0b10;
    --black: #111111;
    --paper: #ffffff;
    --paper-grey: #ecebeb;
    --ink: #2a2a2a;
    --backdrop: #2b2b2b;
  }
  * { box-sizing: border-box; margin: 0; padding: 0; }
  html, body { width: 1200px; height: 800px; overflow: hidden; background: var(--backdrop); }
  body { font-family: "Open Sans", Arial, sans-serif; color: var(--ink); }

  .brochure {
    position: absolute; left: 30px; top: 30px; width: 1140px; height: 740px;
    background: var(--paper); overflow: hidden;
    box-shadow: 0 12px 30px rgba(0,0,0,.5);
  }
  .panel { position: absolute; top: 0; width: 380px; height: 740px; }
  .panel--about { left: 0; background: var(--paper); }
  .panel--difference { left: 380px; background: linear-gradient(180deg, var(--paper) 0%, var(--paper-grey) 100%); }
  .panel--cover { left: 760px; background: linear-gradient(180deg, var(--paper-grey) 0%, #f6f6f6 100%); }
  .fold { position: absolute; top: 0; width: 1px; height: 740px; background: rgba(0,0,0,.08); z-index: 4; }

  .section-header { position: absolute; top: 36px; left: 0; display: flex; height: 32px; }
  .section-tab {
    height: 32px; padding: 0 34px 0 30px; white-space: nowrap;
    background: var(--red); color: #fff; font-weight: 600; font-size: 16px; line-height: 32px;
    clip-path: polygon(0 0, 100% 0, calc(100% - 16px) 100%, 0 100%);
  }
  .tab-edge {
    width: 30px; height: 32px; margin-left: -14px; background: var(--black);
    clip-path: polygon(16px 0, 30px 0, 14px 100%, 0 100%);
  }
  .section-rule { position: absolute; top: 66px; left: 0; width: 380px; height: 3px; background: var(--red); }

  .lead {
    position: absolute; left: 30px; right: 26px; top: 86px;
    color: var(--red); font-weight: 700; font-size: 13.5px; line-height: 1.3;
  }
  .about-copy {
    position: absolute; left: 30px; right: 26px; top: 130px;
    font-size: 11.2px; line-height: 1.55; text-align: justify;
  }

  .photo { position: absolute; }
  .photo--professional {
    left: 0; top: 350px; width: 380px; height: 290px;
    background: linear-gradient(160deg, #f4f6f8 0%, #dfe4ea 45%, #9aa8bc 100%);
  }
  .photo--team {
    left: 380px; top: 250px; width: 760px; height: 420px;
    background: linear-gradient(150deg, #d9dcdf 0%, #c8cdd2 40%, #b5a8a0 70%, #e9e4e0 100%);
    clip-path: polygon(18% 22%, 50% 0, 100% 0, 100% 100%, 0 100%, 0 52%);
  }

  .difference-lead {
    position: absolute; left: 24px; right: 22px; top: 86px;
    color: var(--red); font-weight: 700; font-size: 13.5px; line-height: 1.3;
  }
  .checklist { position: absolute; left: 24px; right: 24px; top: 132px; list-style: none; }
  .checklist li {
    position: relative; padding-left: 22px; margin-bottom: 10px;
    font-size: 11.2px; line-height: 1.5;
  }
  .checklist svg { position: absolute; left: 0; top: 2px; }

  .cover-headline {
    position: absolute; left: 40px; top: 60px; width: 300px;
    color: var(--red); font-weight: 400; font-size: 30px; line-height: 1.2;
  }

  .wave-band { position: absolute; left: 0; top: 0; width: 1140px; height: 740px; z-index: 3; }

  .contact { position: absolute; z-index: 5; color: #fff; }
  .contact--about { left: 0; width: 380px; top: 672px; text-align: center; }
  .contact--about .contact-phone, .contact--about .contact-web { justify-content: center; }
  .contact--cover { right: 30px; top: 672px; }
  .contact--cover .contact-phone, .contact--cover .contact-web { justify-content: flex-end; }
  .contact-phone { font-size: 19px; font-weight: 400; display: flex; align-items: center; gap: 8px; line-height: 1.3; }
  .contact-web { font-size: 12px; display: flex; align-items: center; gap: 6px; margin-top: 4px; white-space: nowrap; }
</style>
</head>
<body>
<main class="brochure">
  <section class="panel panel--about">
    <div class="section-header"><h2 class="section-tab">Who We Are</h2><span class="tab-edge"></span></div>
    <div class="section-rule"></div>
    <h3 class="lead">A Top-Notch Resource for Administrative, Human Resources, and Accounting Talent</h3>
    <p class="about-copy">Morvell Staffing Partners is a professional search firm that specializes in providing top-notch administrative, human resources, and accounting talent. We provide best-in-class talent to companies seeking to simplify their recruiting process, increase efficiency, and optimize productivity. Each search is customized based on our client's unique requirements. We provide quality, timely, and efficient services. Our recruiters are highly skilled in identifying, screening, interviewing, and assessing candidates across various industries. We develop a partnership with our client and candidate in order to make the recruitment process a success for both parties.</p>
    <div class="photo photo--professional" role="img" aria-label="Photo of a smiling business professional in shirt and tie seated at a desk"></div>
  </section>

  <section class="panel panel--difference">
    <div class="section-header"><h2 class="section-tab">Experience the Morvell Difference</h2><span class="tab-edge"></span></div>
    <div class="section-rule"></div>
    <h3 class="difference-lead">We use our proprietary M-Strategy approach to deliver high-quality results.</h3>
    <ul class="checklist">
      <li><svg width="13" height="11" viewBox="0 0 13 11"><path d="M1 6 L5 10 L12 1" fill="none" stroke="#c0141c" stroke-width="2"/></svg>Top-Notch Talent. We will only present candidates who meet 90% of your job requirements.</li>
      <li><svg width="13" height="11" viewBox="0 0 13 11"><path d="M1 6 L5 10 L12 1" fill="none" stroke="#c0141c" stroke-width="2"/></svg>Thorough. We listen to your needs and develop a recruiting checklist to make sure we cover all basis.</li>
      <li><svg width="13" height="11" viewBox="0 0 13 11"><path d="M1 6 L5 10 L12 1" fill="none" stroke="#c0141c" stroke-width="2"/></svg>Tenacious. We are passionate and persistent about meeting your expectations.</li>
      <li><svg width="13" height="11" viewBox="0 0 13 11"><path d="M1 6 L5 10 L12 1" fill="none" stroke="#c0141c" stroke-width="2"/></svg>Timely. We deliver quality results on time.</li>
    </ul>
  </section>

  <section class="panel panel--cover">
    <h1 class="cover-headline">We can find the right talent for your hiring needs.</h1>
  </section>

  <div class="photo photo--team" role="img" aria-label="Photo of a diverse team of business professionals meeting around a glass conference table"></div>

  <svg class="wave-band" viewBox="0 0 1140 740" preserveAspectRatio="none" aria-hidden="true">
    <path d="M0,610 C150,600 300,640 380,655 C560,688 760,660 1140,520 L1140,740 L0,740 Z" fill="#c0141c"/>
    <path d="M0,610 C150,600 300,640 380,655 C560,688 760,660 1140,520" fill="none" stroke="#111" stroke-width="9"/>
    <path d="M0,628 C150,620 300,655 380,668 C560,702 760,676 1140,538" fill="none" stroke="#8e0b10" stroke-width="14"/>
    <path d="M0,650 C150,648 300,672 380,684 C560,722 760,696 1140,558" fill="none" stroke="#ffffff" stroke-width="10"/>
  </svg>

  <div class="fold" style="left:380px"></div>
  <div class="fold" style="left:760px"></div>

  <div class="contact contact--about">
    <p class="contact-phone"><svg width="16" height="16" viewBox="0 0 16 16"><circle cx="8" cy="8" r="7" fill="none" stroke="#fff" stroke-width="1.4"/><path d="M5.2,4.5 L6.6,4.5 L7.2,6.2 L6.3,7 C6.8,8 7.6,8.9 8.8,9.5 L9.6,8.6 L11.3,9.2 L11.3,10.7 C8,11 5,8 5.2,4.5 Z" fill="#fff"/></svg>555-014-2286</p>
    <p class="contact-web"><svg width="11" height="11" viewBox="0 0 12 12"><circle cx="6" cy="6" r="5" fill="none" stroke="#fff" stroke-width="1.2"/><path d="M1,6 H11 M6,1 C3.5,3.5 3.5,8.5 6,11 M6,1 C8.5,3.5 8.5,8.5 6,11" fill="none" stroke="#fff" stroke-width="1"/></svg>www.morvellstaffingpartners.example</p>
  </div>
  <div class="contact contact--cover">
    <p class="contact-phone"><svg width="16" height="16" viewBox="0 0 16 16"><circle cx="8" cy="8" r="7" fill="none" stroke="#fff" stroke-width="1.4"/><path d="M5.2,4.5 L6.6,4.5 L7.2,6.2 L6.3,7 C6.8,8 7.6,8.9 8.8,9.5 L9.6,8.6 L11.3,9.2 L11.3,10.7 C8,11 5,8 5.2,4.5 Z" fill="#fff"/></svg>555-014-2286</p>
    <p class="contact-web"><svg width="11" height="11" viewBox="0 0 12 12"><circle cx="6" cy="6" r="5" fill="none" stroke="#fff" stroke-width="1.2"/><path d="M1,6 H11 M6,1 C3.5,3.5 3.5,8.5 6,11 M6,1 C8.5,3.5 8.5,8.5 6,11" fill="none" stroke="#fff" stroke-width="1"/></svg>www.morvellstaffingpartners.example</p>
  </div>
</main>
</body>
</html>
```